IT Company needs full suite of stationery

Our company 4627 Vantor Holdings Inc. is an IT company based in Toronto, Canada. Based on our logo we would like to see business cards(front and back), letterhead, envelope, brochure template. Design would be simple, not too bright, modern but can be used for many years, good theme throughout. Our official logo is the the fullcolor_a, full company name is 4627 Vantor Holdings Inc., Please include full company name on all pieces. Logo can be modified to be the graphic only with the "4627 Holdings", I have cropped it myself for a couple files but I am no designer. We will provide lots of feedback so post early and often.

Project Deadline Extended
Reason: Very busy around the holidays, like a lot of the designs currently submitted, will definitely be picking one. Thanks for your submissions and merry Christmas and Happy New Year to everyone.

Industry/Entity Type

Business

```html
<!DOCTYPE html>
<html lang="en">
<head>
<meta charset="utf-8">
<title>4627 Holdings – Business Card</title>
<link href="https://fonts.googleapis.com/css2?family=Open+Sans:wght@400;600&display=swap" rel="stylesheet">
<style>
  :root {
    --backdrop: #3a302b;
    --card: #1b1b1c;
    --card-edge: #2a2a2b;
    --green: #3fb24a;
    --silver: #9a9a9c;
    --text: #c9c9c9;
    --rule: #4a4a4a;
  }
  * { margin: 0; padding: 0; box-sizing: border-box; }
  html, body {
    width: 1200px; height: 716px; overflow: hidden;
    background: var(--backdrop);
    font-family: "Open Sans", Arial, sans-serif;
  }
  .stage {
    position: relative; width: 1200px; height: 716px;
    display: flex; align-items: center; justify-content: center; gap: 50px;
  }
  .card {
    width: 520px; height: 297px;
    background: var(--card);
    border: 1px solid var(--card-edge);
    position: relative;
  }
  .brand {
    display: flex; align-items: center; gap: 16px;
  }
  .brand-mark { border-radius: 50%; flex: none; }
  .brand-name { font-weight: 600; white-space: nowrap; }

  /* front */
  .card-front { display: flex; align-items: center; justify-content: center; }
  .card-front .brand-mark { width: 78px; height: 78px; border: 3px solid #2c2c2d; }
  .card-front .brand-name { font-size: 34px; color: var(--silver); }

  /* back */
  .card-back .brand { position: absolute; left: 150px; top: 52px; }
  .card-back .brand-mark { width: 62px; height: 62px; background: var(--green); }
  .card-back .brand-name { font-size: 30px; color: var(--green); }

  .person {
    position: absolute; right: 276px; top: 158px; text-align: right;
    font-size: 11.5px; line-height: 1.5; color: var(--text);
  }
  .person-name { font-size: 16px; font-weight: 600; color: var(--green); line-height: 1.3; }
  .person-company { color: var(--green); }

  .divider {
    position: absolute; left: 258px; top: 168px; width: 1px; height: 82px;
    background: var(--rule);
  }
  .contacts {
    position: absolute; left: 274px; top: 166px;
    list-style: none; font-size: 11.5px; color: var(--text); line-height: 20px;
  }
  .contacts li { display: flex; align-items: center; gap: 10px; }
  .contacts svg { width: 12px; height: 12px; fill: var(--green); flex: none; }
</style>
</head>
<body>
<main class="stage">
  <section class="card card-front" aria-label="Business card front">
    <div class="brand">
      <span class="brand-mark"></span>
      <span class="brand-name">4627 Holdings</span>
    </div>
  </section>

  <section class="card card-back" aria-label="Business card back">
    <div class="brand">
      <span class="brand-mark"></span>
      <span class="brand-name">4627 Holdings</span>
    </div>

    <div class="person">
      <p class="person-name">Daniel Moreau</p>
      <p>President</p>
      <p class="person-company">4627 Vantor Holdings Inc.</p>
      <p>88 Carrow Lane</p>
      <p>Suite 310 Toronto</p>
    </div>

    <div class="divider"></div>

    <ul class="contacts">
      <li>
        <svg viewBox="0 0 12 12"><path d="M2.5 0.5l2 2.5-1 1.2c.7 1.5 1.8 2.6 3.3 3.3l1.2-1 2.5 2-1 2C5 10.5 1.5 7 .5 1.5z"/></svg>
        +1-416-555-0142
      </li>
      <li>
        <svg viewBox="0 0 12 12"><path d="M3 0h6a1 1 0 0 1 1 1v10a1 1 0 0 1-1 1H3a1 1 0 0 1-1-1V1a1 1 0 0 1 1-1zm.5 1.5v7.5h5V1.5z"/></svg>
        +1-416-555-0187
      </li>
      <li>
        <svg viewBox="0 0 12 12"><path d="M0 2h12v1.2L6 7 0 3.2zM0 4.6l6 3.8 6-3.8V10H0z"/></svg>
        info@4627holdings.com
      </li>
      <li>
        <svg viewBox="0 0 12 12"><circle cx="6" cy="6" r="6"/></svg>
        www.4627holdings.com
      </li>
    </ul>
  </section>
</main>
</body>
</html>
```